New profile page for existing party website

For the party website 'Partyvenz' we need a new design for the user profile page.

The page should show
* a profile picture
* basic information like name, age and city
* music styles he/she likes
* links to their Chatterbook profile and website
* a bio (HTML content)
* events they plan to go to
* past events
* pictures

Challenge is that some users may have little information (just their name) while others have a huge description, lots of foto's, events, etc.

Please visit http://www.partyvenz.example and http://www.partyvenz.example/users/bertil

Target Market(s)

Men and women between 18 and 35

Industry/Entity Type

Night Club

Number of Pages Required

2 page

Font styles to use
Other font styles liked:
• Roboto

Requirements
Must have
• Please design how the page looks with a fully filled out profile and with an empty profile.
• It should fit well with the existing website.
• Include designs for both for small screens (mobile) and large screens (tablet, desktop).
Nice to have
• UX design on how to collapse or paginate sections.
• Interactive effects would be a bonus.
Should not have
• The page should not have subnavigation like menus or tabs.

```html
<!DOCTYPE html>
<html lang="nl">
<head>
<meta charset="utf-8">
<title>Bertil Vos – Partyvenz</title>
<link href="https://fonts.googleapis.com/css2?family=Roboto:wght@300;400;500;700&display=swap" rel="stylesheet">
<style>
:root{
  --page:#1f1f1f;
  --panel:#262626;
  --bar:#0e0e0e;
  --topbar:#151515;
  --text:#e6e6e6;
  --muted:#b9b9b9;
  --white:#ffffff;
  --hero-a:#f4a08f;
  --hero-b:#f08a6a;
  --accent:#ec6f57;
  --badge:rgba(255,255,255,.85);
}
*{box-sizing:border-box;margin:0;padding:0}
html,body{width:1200px;height:4852px;overflow:hidden}
body{background:var(--page);font-family:'Roboto',Arial,sans-serif;color:var(--text);position:relative}
svg.defs{position:absolute;width:0;height:0}
.icon{width:16px;height:16px;fill:var(--white);flex:none}

/* top bar */
.topbar{position:absolute;left:0;top:0;width:1200px;height:58px;background:var(--topbar);display:flex;align-items:center;padding:0 32px}
.brand{font-weight:700;font-size:26px;color:var(--white);display:flex;align-items:center;gap:8px}
.brand-dot{width:12px;height:12px;border-radius:50%;background:var(--accent)}
.nav{margin-left:auto;display:flex;align-items:center;gap:22px;font-size:15px;color:var(--white)}
.search{width:146px;height:30px;background:#fff;border-radius:2px;color:#888;font-size:13px;padding:7px 8px}
.user{display:flex;align-items:center;gap:8px}
.user-avatar{width:34px;height:34px;border-radius:3px;background:linear-gradient(135deg,#c98b5e,#5a3a28)}
.caret{width:0;height:0;border-left:4px solid transparent;border-right:4px solid transparent;border-top:5px solid #fff}

/* hero */
.hero{position:absolute;left:0;top:58px;width:1200px;height:314px;background:linear-gradient(100deg,var(--hero-a),var(--hero-b) 55%,#f5b09a)}
.portrait{position:absolute;left:136px;top:39px;width:200px;height:218px;border:5px solid #fff;background:linear-gradient(160deg,#e8dcc8,#b98a62 55%,#6a4430)}
.profile{position:absolute;left:420px;top:48px;color:var(--white)}
.profile h1{font-weight:300;font-size:32px;letter-spacing:.5px}
.since{font-size:12px;margin-top:4px;opacity:.9}
.facts{margin-top:18px;font-size:17px;line-height:30px}
.facts b{font-weight:700}
.facts span{font-weight:300}
.socials{display:flex;gap:14px;margin-top:20px}
.social{width:30px;height:30px;display:flex;align-items:center;justify-content:center}
.social-square{width:24px;height:24px;background:#fff;border-radius:3px}
.btn-message{position:absolute;right:20px;top:13px;width:97px;height:26px;background:var(--accent);color:#fff;font-size:12px;display:flex;align-items:center;justify-content:center;border-radius:2px}

/* sections */
.section{position:absolute;left:10px;width:1180px}
.section-head{height:48px;background:var(--bar);display:flex;align-items:center;justify-content:space-between;padding:0 22px}
.section-head h2{font-size:24px;font-weight:500;color:var(--white)}
.chev{width:22px;height:14px}
.section-body{background:var(--panel);padding:0 22px}

/* bio */
.bio{font-size:14px;line-height:23px;color:var(--text);padding-top:22px;padding-bottom:20px}
.bio h3{font-size:18px;font-weight:500;color:var(--white);margin-bottom:14px}
.bio p{margin-bottom:12px}

/* event cards */
.event-grid{display:grid;grid-template-columns:556px 556px;column-gap:24px;row-gap:20px;padding-top:34px;padding-bottom:30px}
.event-card{height:352px}
.banner{position:relative;height:143px;width:100%}
.date-badge{position:absolute;right:0;top:0;background:var(--badge);color:#222;font-size:13px;padding:4px 10px}
.event-title{font-size:17px;font-weight:500;color:var(--white);margin:18px 0 10px}
.meta{list-style:none;font-size:12px;color:var(--text)}
.meta li{display:flex;align-items:flex-start;gap:12px;line-height:16px;margin-bottom:16px}
.meta .icon{width:14px;height:14px;margin-left:16px}
.meta li.note{font-weight:700}

/* event list */
.event-list{padding-top:28px;padding-bottom:10px}
.event-row{display:flex;gap:30px;height:204px}
.event-row .banner{width:379px;height:146px;flex:none}
.event-row .event-title{margin:2px 0 12px;font-size:15px}
.event-row .meta li{margin-bottom:14px}
.event-row .meta .icon{margin-left:10px}

/* photos */
.photo-grid{display:grid;grid-template-columns:repeat(6,1fr);grid-auto-rows:182px;gap:8px;padding:26px 12px 30px}
.photo{background:linear-gradient(150deg,#d9c7b0,#c46a2c 60%,#4b3326)}
.photo.big{grid-column:span 2;grid-row:span 2}
.photo.v2{background:linear-gradient(160deg,#ece4d6,#e07a2a 55%,#3a2a22)}
.photo.v3{background:linear-gradient(140deg,#6d6a66,#2e2a28 50%,#d06a2a)}
.photo.v4{background:linear-gradient(170deg,#a8b0b8,#e58a3a 60%,#5a3c2a)}

/* banners */
.b-latin{background:linear-gradient(120deg,#0f5a1e,#2f9a2e 45%,#6cc23c 70%,#e9d21a)}
.b-klank{background:linear-gradient(120deg,#d7efe8,#a6dccd 50%,#7cc7b6)}
.b-outdoor{background:linear-gradient(110deg,#f4f1ec,#efe6e0 50%,#e2d3f0)}
.b-zonlicht{background:linear-gradient(120deg,#16283d,#243a55 50%,#1a2d44)}

/* footer */
.footer{position:absolute;left:0;top:4740px;width:1200px;height:112px;background:#121212;text-align:center;padding-top:36px}
.footer-links{font-size:13px;font-weight:700;color:var(--white);letter-spacing:.5px}
.footer-links span{margin:0 8px;color:var(--muted);font-weight:400}
.copy{font-size:11px;color:var(--muted);margin-top:14px}
</style>
</head>
<body>

<svg class="defs" aria-hidden="true">
  <defs>
    <symbol id="i-pin" viewBox="0 0 16 16"><path d="M8 1a5 5 0 0 0-5 5c0 4 5 9 5 9s5-5 5-9a5 5 0 0 0-5-5zm0 7a2 2 0 1 1 0-4 2 2 0 0 1 0 4z"/></symbol>
    <symbol id="i-note" viewBox="0 0 16 16"><path d="M6 2l8-1.5v10a2.2 2.2 0 1 1-1.5-2V4L7.5 5v7.5a2.2 2.2 0 1 1-1.5-2z"/></symbol>
    <symbol id="i-clock" viewBox="0 0 16 16"><path d="M8 1a7 7 0 1 0 0 14A7 7 0 0 0 8 1zm0 1.8a5.2 5.2 0 1 1 0 10.4A5.2 5.2 0 0 1 8 2.8zM7.2 4v4.6l3.3 2 .8-1.2-2.6-1.6V4z"/></symbol>
    <symbol id="i-tag" viewBox="0 0 16 16"><path d="M1 1h6.5l7.5 7.5-6.5 6.5L1 7.5zm3.5 2a1.5 1.5 0 1 0 0 3 1.5 1.5 0 0 0 0-3z"/></symbol>
    <symbol id="i-chev" viewBox="0 0 22 14"><path d="M2 2l9 9 9-9" fill="none" stroke="#fff" stroke-width="3.5"/></symbol>
  </defs>
</svg>

<header class="topbar">
  <div class="brand"><span class="brand-dot"></span>Partyvenz</div>
  <nav class="nav">
    <span>Home</span><span>Agenda</span><span>Vrijkaarten</span><span>Foto's</span><span>Nieuws</span>
    <div class="search">Zoeken</div>
    <div class="user"><div class="user-avatar" role="img" aria-label="Kleine profielfoto van de ingelogde gebruiker"></div>Bertil Vos<span class="caret"></span></div>
  </nav>
</header>

<section class="hero">
  <div class="portrait" role="img" aria-label="Profielfoto van Bertil Vos"></div>
  <div class="profile">
    <h1>Bertil Vos</h1>
    <div class="since">Member since May 24, 2006</div>
    <div class="facts">
      <div><b>Age :</b> <span>34</span></div>
      <div><b>City :</b> <span>Amsterdam</span></div>
      <div><b>Music :</b> <span>Latin / Salsa</span></div>
    </div>
    <div class="socials">
      <div class="social" aria-label="Chatterbook"><div class="social-square"></div></div>
      <div class="social" aria-label="Streamtube"><div class="social-square"></div></div>
      <div class="social" aria-label="Website">
        <svg width="26" height="26" viewBox="0 0 26 26"><circle cx="13" cy="13" r="11" fill="none" stroke="#fff" stroke-width="2.2"/><ellipse cx="13" cy="13" rx="5" ry="11" fill="none" stroke="#fff" stroke-width="2"/><path d="M2 13h22M4 7h18M4 19h18" stroke="#fff" stroke-width="1.8"/></svg>
      </div>
      <div class="social" aria-label="E-mail">
        <svg width="28" height="22" viewBox="0 0 28 22"><rect x="1" y="1" width="26" height="20" rx="2" fill="#fff"/><path d="M2 3l12 9 12-9" fill="none" stroke="#f08a6a" stroke-width="2"/></svg>
      </div>
    </div>
  </div>
  <div class="btn-message">Message</div>
</section>

<section class="section" style="top:398px">
  <div class="section-head"><h2>Biography</h2><svg class="chev"><use href="#i-chev"/></svg></div>
  <div class="section-body bio" style="height:1010px">
    <h3>NickV Photography</h3>
    <p>Function : Head promotions, photographer, communication, marketing, and sales.</p>
    <p>Active since : jan 2006</p>
    <p>Shoots : 500 and counting</p>
    <p>Wil jij fotograferen voor Partyvenz?</p>
    <p>Als je uitgaan leuk vindt, makkelijk bent in de omgang en uiteraard houdt van fotograferen, biedt Partyvenz je de kans een kijkje te nemen in de wereld van de partyfotografie. Door de inzet van de fotografen is Partyvenz uitgegroeid tot een van de meest toonaangevende partysites van Nederland. De betrouwbaarheid, de hoge kwaliteit van de foto's en het coveren van de belangrijkste evenementen maakt van Partyvenz een van de best bezochte websites in ons vakgebied.</p>
    <p>Belangrijk informatie</p>
    <p>Fotograferen voor Partyvenz is op vrijwillige basis. Je kan kiezen waar en wanneer je uitgaat en foto's maakt, maar een vaste inbreng word wel van je verwacht. Hoe meer je voor Partyvenz doet, hoe meer ervaring je opdoet met de camera en hoe beter je wordt. Hierdoor kan je weer naar interessantere feesten en festivals. Wat je wel krijgt is gratis entree voor een evenement en soms ook andere voordelen zoals gratis drankjes... Je gaat meestal met je tweetjes op pad en ontmoet veel nieuwe mensen zoals DJ's en organisatoren. Hoe meer je voor Partyvenz werkt hoe meer ervaring je er ook uit zal halen. De beste fotografen doen de leukste en de meest uitdagende evenementen bijvoorbeeld: Paleis Weekender, Outer Rim Outdoor, Zonlicht Weekend, Meerdans etc.</p>
    <p>Voorwaarden</p>
    <p>- Je moet 18 jaar of ouder zijn.<br>
    - Je moet het aankunnen om hoge kwaliteit foto's te maken en professioneel gedrag vertonen.<br>
    - Je moet sociaal zijn; een open persoon zijn die ervan houdt om andere mensen te ontmoeten.<br>
    - Het is een vereiste dat je een digitale spiegelreflex-camera hebt en een lichtsterke lens met vast diafragma van F2.8 en natuurlijk een externe flitser (E-TTL).<br>
    - Je bent verantwoordelijk voor je eigen vervoer om naar de evenementen te gaan waar je foto's maakt.</p>
    <p>Aanmelden<br>
    Wil jij ook het team van Partyvenz versterken en het nachtleven van een andere kant verkennen? Geef je dan op, stuur een mailtje naar nick@partyvenz.example Vermeld daar goed in je naam, leeftijd, woonplaats en het type camera dat je hebt en je ervaring op het gebied van fotograferen.</p>
    <p>Bekijk ons online foto album voor de door mij geschoten foto's. Bekijk al mijn filmpjes via mijn eigen Streamtube kanaal</p>
  </div>
</section>

<section class="section" style="top:1482px">
  <div class="section-head"><h2>Geplande evenementen (18)</h2><svg class="chev"><use href="#i-chev"/></svg></div>
  <div class="section-body event-grid">
    <article class="event-card">
      <div class="banner b-latin" role="img" aria-label="Festivalbanner met tropische bladeren en datum"><span class="date-badge">20 augustus 2016</span></div>
      <h3 class="event-title">Recreatiepark Zeewijde</h3>
      <ul class="meta">
        <li><svg class="icon"><use href="#i-pin"/></svg>Sportpark Molenhaven, Amsterdam</li>
        <li><svg class="icon"><use href="#i-note"/></svg>Live / Soul / Techno / Uk</li>
        <li><svg class="icon"><use href="#i-clock"/></svg>12.00 - 23.00 uur</li>
        <li class="note"><svg class="icon"><use href="#i-tag"/></svg>Pre-register now for KLANK_WERK Festival 2016 at: · http://klankwerkfestival.example/</li>
      </ul>
    </article>
    <article class="event-card">
      <div class="banner b-klank" role="img" aria-label="Festivalbanner in mintgroene tinten"><span class="date-badge">20 augustus 2016</span></div>
      <h3 class="event-title">Klank_werk Festival 2016</h3>
      <ul class="meta">
        <li><svg class="icon"><use href="#i-pin"/></svg>Sportpark Molenhaven, Amsterdam</li>
        <li><svg class="icon"><use href="#i-note"/></svg>Live / Soul / Techno / Uk</li>
        <li><svg class="icon"><use href="#i-clock"/></svg>12.00 - 23.00 uur</li>
        <li class="note"><svg class="icon"><use href="#i-tag"/></svg>Pre-register now for KLANK_WERK Festival 2016 at: · http://klankwerkfestival.example/</li>
      </ul>
    </article>
    <article class="event-card">
      <div class="banner b-klank" role="img" aria-label="Festivalbanner in mintgroene tinten"><span class="date-badge">20 augustus 2016</span></div>
      <h3 class="event-title">Klank_werk Festival 2016</h3>
      <ul class="meta">
        <li><svg class="icon"><use href="#i-pin"/></svg>Sportpark Molenhaven, Amsterdam</li>
        <li><svg class="icon"><use href="#i-note"/></svg>Live / Soul / Techno / Uk</li>
        <li><svg class="icon"><use href="#i-clock"/></svg>12.00 - 23.00 uur</li>
        <li class="note"><svg class="icon"><use href="#i-tag"/></svg>Pre-register now for KLANK_WERK Festival 2016 at: · http://klankwerkfestival.example/</li>
      </ul>
    </article>
    <article class="event-card">
      <div class="banner b-latin" role="img" aria-label="Festivalbanner met tropische bladeren en datum"><span class="date-badge">20 augustus 2016</span></div>
      <h3 class="event-title">Recreatiepark Zeewijde</h3>
      <ul class="meta">
        <li><svg class="icon"><use href="#i-pin"/></svg>Sportpark Molenhaven, Amsterdam</li>
        <li><svg class="icon"><use href="#i-note"/></svg>Live / Soul / Techno / Uk</li>
        <li><svg class="icon"><use href="#i-clock"/></svg>12.00 - 23.00 uur</li>
        <li class="note"><svg class="icon"><use href="#i-tag"/></svg>Pre-register now for KLANK_WERK Festival 2016 at: · http://klankwerkfestival.example/</li>
      </ul>
    </article>
    <article class="event-card">
      <div class="banner b-latin" role="img" aria-label="Festivalbanner met tropische bladeren en datum"><span class="date-badge">20 augustus 2016</span></div>
      <h3 class="event-title">Recreatiepark Zeewijde</h3>
      <ul class="meta">
        <li><svg class="icon"><use href="#i-pin"/></svg>Sportpark Molenhaven, Amsterdam</li>
        <li><svg class="icon"><use href="#i-note"/></svg>Live / Soul / Techno / Uk</li>
        <li><svg class="icon"><use href="#i-clock"/></svg>12.00 - 23.00 uur</li>
        <li class="note"><svg class="icon"><use href="#i-tag"/></svg>Pre-register now for KLANK_WERK Festival 2016 at: · http://klankwerkfestival.example/</li>
      </ul>
    </article>
    <article class="event-card">
      <div class="banner b-klank" role="img" aria-label="Festivalbanner in mintgroene tinten"><span class="date-badge">20 augustus 2016</span></div>
      <h3 class="event-title">Klank_werk Festival 2016</h3>
      <ul class="meta">
        <li><svg class="icon"><use href="#i-pin"/></svg>Sportpark Molenhaven, Amsterdam</li>
        <li><svg class="icon"><use href="#i-note"/></svg>Live / Soul / Techno / Uk</li>
        <li><svg class="icon"><use href="#i-clock"/></svg>12.00 - 23.00 uur</li>
        <li class="note"><svg class="icon"><use href="#i-tag"/></svg>Pre-register now for KLANK_WERK Festival 2016 at: · http://klankwerkfestival.example/</li>
      </ul>
    </article>
  </div>
</section>

<section class="section" style="top:2724px">
  <div class="section-head"><h2>Geplande evenementen (18)</h2><svg class="chev"><use href="#i-chev"/></svg></div>
  <div class="section-body event-list" style="height:1058px">
    <article class="event-row">
      <div class="banner b-outdoor" role="img" aria-label="Lichte festivalflyer met kleurrijke line-up"><span class="date-badge">20 augustus 2016</span></div>
      <div><h3 class="event-title">Recreatiepark Zeewijde</h3>
      <ul class="meta">
        <li><svg class="icon"><use href="#i-pin"/></svg>Sportpark Molenhaven, Amsterdam</li>
        <li><svg class="icon"><use href="#i-note"/></svg>Live / Soul / Techno / Uk</li>
        <li><svg class="icon"><use href="#i-clock"/></svg>12.00 - 23.00 uur</li>
        <li class="note"><svg class="icon"><use href="#i-tag"/></svg>Pre-register now for KLANK_WERK Festival 2016 at: · http://klankwerkfestival.example/</li>
      </ul></div>
    </article>
    <article class="event-row">
      <div class="banner b-zonlicht" role="img" aria-label="Donkerblauwe festivalflyer met geel kader"><span class="date-badge">20 augustus 2016</span></div>
      <div><h3 class="event-title">Klank_werk Festival 2016</h3>
      <ul class="meta">
        <li><svg class="icon"><use href="#i-pin"/></svg>Sportpark Molenhaven, Amsterdam</li>
        <li><svg class="icon"><use href="#i-note"/></svg>Live / Soul / Techno / Uk</li>
        <li><svg class="icon"><use href="#i-clock"/></svg>12.00 - 23.00 uur</li>
        <li class="note"><svg class="icon"><use href="#i-tag"/></svg>Pre-register now for KLANK_WERK Festival 2016 at: · http://klankwerkfestival.example/</li>
      </ul></div>
    </article>
    <article class="event-row">
      <div class="banner b-outdoor" role="img" aria-label="Lichte festivalflyer met kleurrijke line-up"><span class="date-badge">20 augustus 2016</span></div>
      <div><h3 class="event-title">Recreatiepark Zeewijde</h3>
      <ul class="meta">
        <li><svg class="icon"><use href="#i-pin"/></svg>Sportpark Molenhaven, Amsterdam</li>
        <li><svg class="icon"><use href="#i-note"/></svg>Live / Soul / Techno / Uk</li>
        <li><svg class="icon"><use href="#i-clock"/></svg>12.00 - 23.00 uur</li>
        <li class="note"><svg class="icon"><use href="#i-tag"/></svg>Pre-register now for KLANK_WERK Festival 2016 at: · http://klankwerkfestival.example/</li>
      </ul></div>
    </article>
    <article class="event-row">
      <div class="banner b-zonlicht" role="img" aria-label="Donkerblauwe festivalflyer met geel kader"><span class="date-badge">20 augustus 2016</span></div>
      <div><h3 class="event-title">Klank_werk Festival 2016</h3>
      <ul class="meta">
        <li><svg class="icon"><use href="#i-pin"/></svg>Sportpark Molenhaven, Amsterdam</li>
        <li><svg class="icon"><use href="#i-note"/></svg>Live / Soul / Techno / Uk</li>
        <li><svg class="icon"><use href="#i-clock"/></svg>12.00 - 23.00 uur</li>
        <li class="note"><svg class="icon"><use href="#i-tag"/></svg>Pre-register now for KLANK_WERK Festival 2016 at: · http://klankwerkfestival.example/</li>
      </ul></div>
    </article>
    <article class="event-row">
      <div class="banner b-outdoor" role="img" aria-label="Lichte festivalflyer met kleurrijke line-up"><span class="date-badge">20 augustus 2016</span></div>
      <div><h3 class="event-title">Recreatiepark Zeewijde</h3>
      <ul class="meta">
        <li><svg class="icon"><use href="#i-pin"/></svg>Sportpark Molenhaven, Amsterdam</li>
        <li><svg class="icon"><use href="#i-note"/></svg>Live / Soul / Techno / Uk</li>
        <li><svg class="icon"><use href="#i-clock"/></svg>12.00 - 23.00 uur</li>
        <li class="note"><svg class="icon"><use href="#i-tag"/></svg>Pre-register now for KLANK_WERK Festival 2016 at: · http://klankwerkfestival.example/</li>
      </ul></div>
    </article>
  </div>
</section>

<section class="section" style="top:3850px">
  <div class="section-head"><h2>Foto's (575)</h2><svg class="chev"><use href="#i-chev"/></svg></div>
  <div class="section-body photo-grid" style="padding-left:12px;padding-right:12px">
    <div class="photo big v2" role="img" aria-label="Partyfoto: feestganger met hoed op Koningsdag"></div>
    <div class="photo" role="img" aria-label="Partyfoto: feestgangers in oranje"></div>
    <div class="photo v4" role="img" aria-label="Partyfoto: vrienden op straat"></div>
    <div class="photo v2" role="img" aria-label="Partyfoto: groep in oranje kleding"></div>
    <div class="photo" role="img" aria-label="Partyfoto: feestgangers buiten"></div>
    <div class="photo v3" role="img" aria-label="Partyfoto: avondfeest binnen"></div>
    <div class="photo v4" role="img" aria-label="Partyfoto: feestgangers aan de gracht"></div>
    <div class="photo v3" role="img" aria-label="Partyfoto: duo op een feest"></div>
    <div class="photo" role="img" aria-label="Partyfoto: feestgangers in oranje"></div>
    <div class="photo v2" role="img" aria-label="Partyfoto: lachende groep"></div>
    <div class="photo v4" role="img" aria-label="Partyfoto: straatfeest"></div>
    <div class="photo" role="img" aria-label="Partyfoto: feestgangers in oranje"></div>
    <div class="photo v3" role="img" aria-label="Partyfoto: groep bij een bar"></div>
    <div class="photo v2" role="img" aria-label="Partyfoto: vrienden buiten"></div>
    <div class="photo v4" role="img" aria-label="Partyfoto: feestgangers op een boot"></div>
    <div class="photo" role="img" aria-label="Partyfoto: groep in oranje"></div>
    <div class="photo v3" role="img" aria-label="Partyfoto: duo in een club"></div>
    <div class="photo v2" role="img" aria-label="Partyfoto: feestgangers met petten"></div>
    <div class="photo v4" role="img" aria-label="Partyfoto: straatfeest"></div>
    <div class="photo" role="img" aria-label="Partyfoto: feestgangers in oranje"></div>
    <div class="photo v3" role="img" aria-label="Partyfoto: groep op een terras"></div>
  </div>
</section>

<footer class="footer">
  <div class="footer-links">CONTACT<span>|</span>GEBRUIKERSVOORWAARDEN<span>|</span>PRIVACY POLICY</div>
  <div class="copy">© 2004-2016 Partyvenz</div>
</footer>

</body>
</html>
```